Brightfold Power - Company Brochure / Display Folder / DL Flyer

We are a trader in environmental commodities based in Australia and require the following 4 designs for an upcoming exhibition;
1) Brochure Folder
Essentially this will be a presentation folder for a number of A4 sheets and will allow us to present business cards. We would like it based on the same design as our stand background - please see attached (001) for reference.
I have attached a file (002) that is basically what i am after, if you could recreate this or something similar it be sufficient. Please change the blue lines to green and incorporate an image that represents solar / environment / renewable energy etc.
Please include our logo (003) as well as the words 'experts in environmental commodity trading'
The back of the folder should have our address, contact number, homepage etc - please refer to the website for these details www.brightfoldpower.com.au.
The template is included also, please ensure the deisgn fits within these boundaries for printing (004 / Forme 8)
2) A4 Flyer
We are after a re design of an old flyer that highlights what we do as a business. I have included the wording for this (005) but am open to interpretations as to designs. Please keep it relevant to the graphics requested for the presentation folder.
This will be a single page A4 sheet - very easy.
3) DL Brochure
We will be running a promotion at the exhibition for cash rewards and need a double sided DL flyer designed so the can be handed out. The back of the flyer should have our logo as well as the green graphics consistent with the stand design / background while the front needs to highlight the following promotional offer;
Brightfold Power Cash Rewards Offer
Get more out of your STC's -trade with us to receive instant cash back!
Trade 1000 STC - receive $250 cash rewards card
Trade 5000 STC - receive $500 cash rewards card
(x1 card on the first 1000 + x2 more cards on the first 5000)
Cash rewards cards are valid everywhere that accepts eftpos - cash can even be withdrawn at ATMS!
Offer valid until October 31st 2014
Unregistered Trade Only.
Please keep this text to the left and incorporate an image or graphic on the right side. One that is professional, ties in with the notion of environmental trading but highlights the offer.
Again we open to interpretations with this one.
4) Card Design
Very basic - a design is needed for the rewards card mentioned in the promotion above. I have attached the template / outline required for this (006/ 007) and basically need out logo and a bit of colour on the cash card.
We are open to some ideas but the main thing is being consistent with the stand design that we will be exhibiting in. We like the graphics used and the plain white with the green curved concept. Please ensure the greens from our logo also.
I will do my best to answer any queries you may have, the files should have all the info needed to get started and we usually have a few design amendments after the first drafts are sent through.
Apologies about the timeframe with this one - we are looking to move fast so the earlier submissions will be considered as I can work back and forth with them.
Good Luck
Brightfold Power.

```html
<!DOCTYPE html>
<html lang="en">
<head>
<meta charset="utf-8">
<title>Brightfold Power – Presentation Folder</title>
<link href="https://fonts.googleapis.com/css2?family=Arimo:wght@400;700&display=swap" rel="stylesheet">
<style>
  :root {
    --canvas: #ffffff;
    --paper: #eeefed;
    --paper-light: #fbfbfa;
    --trim: #5a5a5a;
    --die: #222222;
    --text-grey: #6d6e70;
    --brand-green: #1f8f45;
    --green-dark: #2f7d3a;
    --green: #4fa83f;
    --lime: #b8d44a;
    --sky-top: #4b77ad;
    --sky-bottom: #9dbad8;
  }
  html, body {
    margin: 0;
    padding: 0;
    width: 1200px;
    height: 878px;
    overflow: hidden;
    background: var(--canvas);
  }
  .folder {
    position: relative;
    width: 1200px;
    height: 878px;
    font-family: "Arimo", Arial, sans-serif;
  }
  .folder-art {
    position: absolute;
    inset: 0;
  }
  .back-contact {
    position: absolute;
    left: 74px;
    top: 731px;
    margin: 0;
    font-size: 11px;
    font-style: normal;
    line-height: 13px;
    color: var(--text-grey);
  }
  .brand {
    position: absolute;
    left: 908px;
    top: 694px;
    width: 230px;
  }
  .brand-name {
    display: flex;
    align-items: center;
    gap: 8px;
    margin: 0;
    font-size: 22px;
    font-weight: 700;
    color: var(--brand-green);
  }
  .brand-mark {
    width: 14px;
    height: 14px;
    background: var(--brand-green);
    flex: none;
  }
  .brand-tagline {
    margin: 14px 0 0;
    font-size: 9.5px;
    letter-spacing: 0.6px;
    color: var(--text-grey);
  }
</style>
</head>
<body>
<main class="folder">
  <svg class="folder-art" width="1200" height="878" viewBox="0 0 1200 878">
    <defs>
      <radialGradient id="paper-glow" cx="0.5" cy="0.45" r="0.7">
        <stop offset="0" stop-color="var(--paper-light)"/>
        <stop offset="1" stop-color="var(--paper)"/>
      </radialGradient>
      <linearGradient id="cover-art-tone" x1="0" y1="0" x2="0.35" y2="1">
        <stop offset="0" stop-color="var(--sky-top)"/>
        <stop offset="0.35" stop-color="var(--sky-bottom)"/>
        <stop offset="0.6" stop-color="var(--green)"/>
        <stop offset="0.85" stop-color="var(--green-dark)"/>
        <stop offset="1" stop-color="var(--lime)"/>
      </linearGradient>
    </defs>

    <rect class="sheet" x="17" y="17" width="1170" height="848" fill="url(#paper-glow)"/>

    <path class="cover-art" role="img"
          aria-label="Solar panels against a blue sky, framed by a sweeping curved band of greens and yellows"
          d="M605 17 L930 17 C 1000 160, 990 290, 880 420 C 770 550, 700 660, 780 865 L605 865 Z"
          fill="url(#cover-art-tone)"/>

    <g class="trim-lines" fill="none" stroke="var(--trim)" stroke-width="0.8">
      <rect x="32" y="26" width="1147" height="825"/>
      <line x1="605" y1="26" x2="605" y2="851"/>
    </g>

    <g class="die-lines" fill="none" stroke="var(--die)" stroke-width="0.8">
      <path d="M32 327 C 18 340, 6 356, 0 372"/>
      <line x1="0" y1="851" x2="605" y2="851"/>
      <line x1="32" y1="851" x2="32" y2="878"/>
      <line x1="598" y1="851" x2="589" y2="878"/>
    </g>
  </svg>

  <address class="back-contact">
    L12 48 Harbour Lane, Melbourne VIC 3000<br>
    1300 555 014<br>
    www.brightfoldpower.com.au
  </address>

  <div class="brand">
    <p class="brand-name"><span class="brand-mark"></span>Brightfold Power</p>
    <p class="brand-tagline">experts in environmental commodity trading</p>
  </div>
</main>
</body>
</html>
```